K & R Acre Works. Business card design

We need a business card designed for a new business. We have a bulldozer and tractor service. We clear land and make wildlife food plots. We provide disking, bush hogging, and site prep services.
I have attached an image of a business card that I like and would like my business cards to look similar.

Target Market(s)

anyone needing bulldozer and/or tractor services

Industry/Entity Type

Business

Contact Information for Business Card

K & R Acre Works, Operated by 7-T-Ranch
Wade Colton
601-472-3358
wcr4817@fieldmail-example.com

Font styles to use
Sans Serif

Colors

Designer to choose colors to be used in the design.

Requirements
Must have
• image of tractor and bulldozer
• Land Clearing
• Wildlife food plots
• Bush Hogging
• Disking
• Site prep
Nice to have
• i have included a image of a business card that i like. I would like mine to be similar.

```html
<!DOCTYPE html>
<html lang="en">
<head>
<meta charset="utf-8">
<title>K &amp; R Acre Works – Business Card</title>
<link rel="stylesheet" href="https://fonts.googleapis.com/css2?family=Roboto:wght@400;500&family=Roboto+Condensed:wght@700&display=swap">
<style>
  :root {
    --page-bg: #2b2b2b;
    --olive: #9a9436;
    --olive-dark: #7f7a2a;
    --brown: #6b3a12;
    --brown-light: #8a4c18;
    --rule: #f4f1e4;
    --text-light: #ffffff;
    --logo-ink: #3b3f44;
    --photo-green: #5d7a45;
    --photo-yellow: #b8ad3c;
    --photo-orange: #c65a2a;
  }
  * { box-sizing: border-box; margin: 0; padding: 0; }
  html, body {
    width: 1200px; height: 960px; overflow: hidden;
    background: var(--page-bg);
  }
  .business-card {
    position: absolute; left: 300px; top: 309px;
    width: 600px; height: 342px;
    border-radius: 18px; overflow: hidden;
    background: var(--olive);
    font-family: "Roboto", Arial, sans-serif;
    color: var(--text-light);
  }
  .equipment-photo {
    position: absolute; left: 0; top: 0; width: 600px; height: 252px;
    background:
      linear-gradient(180deg, rgba(120,150,110,0.55) 0%, rgba(0,0,0,0) 40%),
      linear-gradient(90deg, var(--photo-green) 0%, var(--photo-yellow) 25%, var(--photo-green) 55%, var(--photo-orange) 80%, var(--photo-orange) 100%);
  }
  .brand {
    position: absolute; left: 148px; top: 78px; width: 306px;
    text-align: center;
  }
  .brand-name {
    display: flex; align-items: center; justify-content: center; gap: 8px;
    font-family: "Roboto Condensed", "Arial Narrow", sans-serif;
    font-weight: 700; font-size: 25px; letter-spacing: 0.5px;
    color: var(--brown-light); line-height: 1;
  }
  .brand-mark { width: 18px; height: 18px; background: var(--olive-dark); }
  .brand-tagline {
    margin-top: 4px;
    font-family: "Roboto Condensed", "Arial Narrow", sans-serif;
    font-weight: 700; font-size: 12.5px; color: var(--logo-ink);
    background: rgba(255,255,255,0.55); padding: 1px 2px;
  }
  .name-tab { position: absolute; left: 0; top: 200px; width: 600px; height: 52px; }
  .holder {
    position: absolute; right: 28px; top: 208px; text-align: right;
  }
  .holder-name {
    font-family: "Roboto Condensed", "Arial Narrow", sans-serif;
    font-weight: 700; font-size: 21px; line-height: 1.05;
  }
  .holder-role { font-size: 14px; font-weight: 500; line-height: 1.3; }
  .divider {
    position: absolute; left: 0; top: 252px; width: 600px; height: 3px;
    background: var(--rule);
  }
  .services {
    position: absolute; left: 30px; top: 271px;
    list-style: none; font-size: 14.5px; line-height: 18px;
  }
  .services .dot { display: inline-block; width: 5px; height: 5px; border-radius: 50%; background: var(--text-light); margin: 0 4px 2px; vertical-align: middle; }
  .contact {
    position: absolute; right: 27px; top: 273px;
    list-style: none; font-size: 14.5px; line-height: 18.5px; text-align: right;
  }
  .contact li { display: flex; justify-content: flex-end; align-items: center; gap: 6px; }
  .contact svg { width: 13px; height: 13px; fill: var(--text-light); }
</style>
</head>
<body>
  <article class="business-card">
    <div class="equipment-photo" role="img" aria-label="Photo of a yellow bulldozer clearing land beside an orange tractor with front loader, trees behind"></div>

    <div class="brand">
      <div class="brand-name"><span class="brand-mark"></span>K &amp; R ACRE WORKS</div>
      <div class="brand-tagline">FOR ALL OF YOUR LAND IMPROVEMENT NEEDS</div>
    </div>

    <svg class="name-tab" viewBox="0 0 600 52" aria-hidden="true">
      <path d="M0 52 L300 52 C330 52 325 4 360 4 L600 4 L600 52 Z" fill="var(--brown)" opacity="0.92"/>
    </svg>
    <div class="holder">
      <div class="holder-name">Wade Colton</div>
      <div class="holder-role">Owner</div>
    </div>

    <div class="divider"></div>

    <ul class="services">
      <li>Land Clearing</li>
      <li>Wildlife food plots</li>
      <li>Bush Hogging<span class="dot"></span>Disking<span class="dot"></span>Site prep</li>
    </ul>

    <ul class="contact">
      <li>601-472-3358
        <svg viewBox="0 0 24 24" aria-hidden="true"><path d="M6.6 10.8a15 15 0 0 0 6.6 6.6l2.2-2.2c.3-.3.7-.4 1-.2 1.1.4 2.3.6 3.6.6.6 0 1 .4 1 1V20c0 .6-.4 1-1 1A17 17 0 0 1 3 4c0-.6.4-1 1-1h3.5c.6 0 1 .4 1 1 0 1.3.2 2.5.6 3.6.1.3 0 .7-.2 1z"/></svg>
      </li>
      <li>wcr4817@fieldmail-example.com
        <svg viewBox="0 0 24 24" aria-hidden="true"><path d="M2 5h20v14H2z M3.5 6.5 12 13l8.5-6.5" fill="none" stroke="#fff" stroke-width="2"/></svg>
      </li>
      <li>kracreworks-example.com
        <svg viewBox="0 0 24 24" aria-hidden="true"><circle cx="12" cy="12" r="10"/><path d="M8 6c2 1 1 3 3 4s-1 3 1 5M15 5c-1 2 1 3 3 3M14 15c1 1 3 1 4 2" stroke="var(--olive)" stroke-width="2" fill="none"/></svg>
      </li>
    </ul>
  </article>
</body>
</html>
```